Black Granite Web Design Project

We are looking for a design for a new company that will be selling Black Granite slabs and tiles. We will be selling to both end-consumers and granite installers. We have already settled on a logo and hopefully this will give an idea of what we like in our designs. We are not going to be selling online but want people to call us so the site is basically an enhanced business card. We will be focusing a lot on SEO so the design will have to keep that in mind.

We would like to keep the design in 1024x768 to make it easily view-able on all devices.

Regarding navigation there should only be a few sub-pages, like "Granite Slabs", "Granite Tiles", "Delivery", "Contact"

Aside from that we are open to designs. One idea we did have was to personalize the site and have a person there somehow to represent the company, making the user feel there are real people behind this site. This is just an idea and not a must.

The name of the company and site is "Copper Ridge Marmora"

Thanks
Updates

Hello All,

Thanks for the great designs. There are some good looking designs that show beautiful kitchens but this site is made for the granite installers and not the retail consumers. So in order not to to confuse the buyers I would like to keep this as much about the raw products as possible. The raw products being the granite slabs, thereby making it obvious we don't sell granite counter tops. 

This design will really be the identity of this company so it is important we get the right message across on this index page and that this page is as complete as possible.

Again, thanks for all the work being put into this.

Target Market(s)

The target audience is granite installers or companies that would with granite slabs.

Industry/Entity Type

Business

```html
<!DOCTYPE html>
<html lang="en">
<head>
<meta charset="utf-8">
<title>Copper Ridge Marmora – Black Granite Slabs and Tiles</title>
<link href="https://fonts.googleapis.com/css2?family=Source+Sans+3:ital,wght@0,300;0,400;0,600;0,700;1,400&display=swap" rel="stylesheet">
<style>
:root{
  --green:#3d5a2c;
  --green-btn:#34502a;
  --ink:#333;
  --muted:#666;
  --header-bg:#ededed;
  --page-bg:#ffffff;
  --panel:#262626;
  --panel-text:#bdbdbd;
  --box-bg:#f4f4f4;
  --box-border:#dcdcdc;
  --footer:#000;
  --footer-text:#cfcfcf;
}
*{box-sizing:border-box;margin:0;padding:0}
html,body{width:1108px;height:1200px;overflow:hidden}
body{background:var(--page-bg);font-family:"Source Sans 3",sans-serif;color:var(--ink);position:relative}
a{color:inherit;text-decoration:none}
.abs{position:absolute}

.site-header{position:absolute;left:0;top:0;width:1108px;height:133px;background:linear-gradient(#f2f2f2,#e8e8e8)}
.util-links{position:absolute;right:282px;top:17px;font-size:13px;color:#555;white-space:nowrap}
.util-links .sep{color:var(--green);margin:0 5px}
.util-links strong{font-weight:700;color:#222}
.search{position:absolute;left:840px;top:12px;width:148px;height:28px;background:#fff;border:1px solid #bbb;border-radius:3px;font-size:10px;font-style:italic;color:#999;padding:8px 8px}
.search svg{position:absolute;right:6px;top:5px}
.brand{position:absolute;left:128px;top:68px;display:flex;align-items:center;gap:10px}
.brand .mark{width:34px;height:34px;background:var(--green)}
.brand .name{font-size:23px;font-weight:700;color:#1a1a1a;letter-spacing:-.2px;line-height:1}
.brand .sub{font-size:10px;font-weight:700;color:#1a1a1a;letter-spacing:1px;margin-top:3px}
.main-nav{position:absolute;right:120px;top:90px;font-size:15px;color:#444}
.main-nav a.active{color:var(--green);font-weight:600}
.main-nav .sep{margin:0 9px;color:#555}

.hero{position:absolute;left:120px;top:143px;width:868px;height:340px;border:3px solid #e6e6e6;border-radius:3px;overflow:hidden}
.hero .photo{position:absolute;inset:0;background:linear-gradient(100deg,#2a2a2a 0%,#3a3a3a 45%,#8a8a8a 55%,#2b2b2b 70%,#3d4656 100%)}
.hero h1{position:absolute;left:27px;top:140px;font-weight:300;font-size:33px;line-height:38px;color:#fff}
.dots{position:absolute;left:29px;top:305px;display:flex;gap:7px}
.dots span{width:17px;height:17px;border-radius:50%;background:#9a9a9a}
.dots span.on{background:#fff}

.welcome h2{position:absolute;left:121px;top:503px;font-size:22px;font-weight:400;color:var(--green)}
.welcome p{position:absolute;left:120px;top:537px;width:630px;font-size:12px;line-height:21.3px;color:#555}
.welcome .more{position:absolute;left:121px;top:648px;font-size:12px;font-weight:600;color:#444}
.welcome .pic{position:absolute;left:785px;top:543px;width:203px;height:117px;border:2px solid #ccc;background:linear-gradient(160deg,#8b8b8b,#4a4a4a 60%,#6d6457)}

.products{position:absolute;left:120px;top:678px;width:868px;height:280px;background:var(--panel);border-radius:3px;overflow:hidden}
.products h3{position:absolute;top:15px;font-size:21px;font-weight:400;color:#eee}
.arrows{position:absolute;top:20px;display:flex;gap:4px}
.arrows span{width:19px;height:19px;border-radius:50%;background:#e5e5e5;display:flex;align-items:center;justify-content:center}
.card{position:absolute;top:56px;width:176px}
.card .thumb{width:176px;height:108px;border:2px solid #ddd}
.card h4{margin-top:9px;font-size:15px;font-weight:400;color:#f2f2f2}
.card p{margin-top:4px;width:165px;font-size:12px;line-height:19px;color:var(--panel-text)}
.card .price{margin-top:4px;font-size:12px;line-height:14px;color:#bbb}
.card .price b{display:block;color:#fff;font-weight:700}

.box{position:absolute;top:970px;width:278px;height:120px;background:var(--box-bg);border:2px solid var(--box-border);border-radius:3px}
.box h3{position:absolute;left:13px;top:6px;font-size:21px;font-weight:400;color:var(--green)}
.box p{font-size:12px;line-height:17px;color:#333}
.signup-field{position:absolute;left:72px;top:44px;width:188px;height:31px;background:#fff;border:1px solid #bbb;border-radius:4px;font-size:12px;font-style:italic;color:#888;padding:7px 13px}
.signup-btn{position:absolute;left:196px;top:84px;width:62px;height:27px;background:var(--green-btn);color:#fff;border-radius:3px;font-size:12px;font-weight:600;text-align:center;line-height:27px}

.site-footer{position:absolute;left:0;top:1103px;width:1108px;height:97px;background:var(--footer);color:var(--footer-text)}
.site-footer h5{font-size:14px;font-weight:600;color:#fff}
.site-footer small{font-size:10px;line-height:18px}
.social{display:flex;gap:9px;margin-top:7px}
.social span{width:30px;height:30px;border-radius:50%;background:#8a8a8a}
</style>
</head>
<body>

<header class="site-header">
  <div class="util-links"><a href="#">Log in</a><span class="sep">|</span><strong>FREE</strong> <a href="#" style="color:var(--green)">Register</a><span class="sep">|</span><a href="#" style="color:var(--green)">FAQ</a></div>
  <div class="search">Search Products..
    <svg width="20" height="18" viewBox="0 0 20 18"><circle cx="7" cy="7" r="5" fill="none" stroke="#333" stroke-width="2.2"/><line x1="11" y1="11" x2="18" y2="16" stroke="#333" stroke-width="3.2" stroke-linecap="round"/></svg>
  </div>
  <a class="brand" href="#">
    <span class="mark"></span>
    <span><span class="name">Copper Ridge Marmora</span><span class="sub" style="display:block">RIO DE JANEIRO</span></span>
  </a>
  <nav class="main-nav">
    <a class="active" href="#">Home</a><span class="sep">|</span><a href="#">Granit Slabs</a><span class="sep">|</span><a href="#">Granite Tiles</a><span class="sep">|</span><a href="#">Delivery</a><span class="sep">|</span><a href="#">Contact</a>
  </nav>
</header>

<section class="hero">
  <div class="photo" role="img" aria-label="Photo of polished black granite slabs standing in a stone yard"></div>
  <h1>We Sell Square Shaped<br>Black Granite Slabs and Titles.</h1>
  <div class="dots"><span class="on"></span><span></span><span></span><span></span></div>
</section>

<section class="welcome">
  <h2>Welcome to Our Site</h2>
  <p>Aliquam molestie, mi et imperdiet euismod, dui purus auctor tellus, et interdum lacus lectus et ante. Sed accumsan sollicitudin sapien, sit amet adipiscing turpis gravida ac. In congue, neque ac lobortis volutpat, libero mauris varius mi, vitae suscipit ipsum ligula vitae risus. Duis aliquam nibh a dui iaculis viverra id a velit. Vivamus egestas risus in magna varius commodo. Sed semper viverra egestas. Etiam pretium porttitor lectus, vel ornare neque porta volutpat.</p>
  <a class="more" href="#">READ MORE &gt;&gt;</a>
  <div class="pic" role="img" aria-label="Photo of stacked grey granite slabs"></div>
</section>

<section class="products">
  <h3 style="left:19px">Granit Slabs</h3>
  <div class="arrows" style="left:357px">
    <span><svg width="8" height="8" viewBox="0 0 8 8"><path d="M5 1L2 4l3 3" fill="none" stroke="#777" stroke-width="1.6"/></svg></span>
    <span><svg width="8" height="8" viewBox="0 0 8 8"><path d="M3 1l3 3-3 3" fill="none" stroke="#333" stroke-width="1.6"/></svg></span>
  </div>
  <h3 style="left:464px">Granite Tiles</h3>
  <div class="arrows" style="left:802px">
    <span><svg width="8" height="8" viewBox="0 0 8 8"><path d="M5 1L2 4l3 3" fill="none" stroke="#777" stroke-width="1.6"/></svg></span>
    <span><svg width="8" height="8" viewBox="0 0 8 8"><path d="M3 1l3 3-3 3" fill="none" stroke="#333" stroke-width="1.6"/></svg></span>
  </div>

  <article class="card" style="left:19px">
    <div class="thumb" role="img" aria-label="Photo of a veined dark granite slab" style="background:linear-gradient(135deg,#6a5f5c,#4f4a4c 50%,#7a6d66)"></div>
    <h4>Mongolian Black Granit</h4>
    <p>Ut wisi enim ad minim veniam quis nostrud exerci..</p>
    <div class="price">Unit Price:<b>US $ 28 / Sq Mtr Min</b></div>
  </article>
  <article class="card" style="left:222px">
    <div class="thumb" role="img" aria-label="Photo of a speckled grey granite slab on a pallet" style="background:linear-gradient(160deg,#9a9a9a,#b8b8b8 50%,#8f8a80)"></div>
    <h4>Mongolian Black Granit</h4>
    <p>Ut wisi enim ad minim veniam quis nostrud exerci..</p>
    <div class="price">Unit Price:<b>US $ 28 / Sq Mtr Min</b></div>
  </article>
  <article class="card" style="left:464px">
    <div class="thumb" role="img" aria-label="Photo of two square black granite tiles" style="background:linear-gradient(150deg,#f2f2f2 0%,#e6e6e6 30%,#2a2a2a 31%,#3a3a3a 80%,#eee 81%)"></div>
    <h4>Black Granite Tiles</h4>
    <p>Ut wisi enim ad minim veniam quis nostrud exerci..</p>
    <div class="price">Unit Price:<b>US $ 28 / Sq Mtr Min</b></div>
  </article>
  <article class="card" style="left:667px">
    <div class="thumb" role="img" aria-label="Photo of speckled dark granite tiles" style="background:linear-gradient(150deg,#4a5058,#5d636b 50%,#3c4047)"></div>
    <h4>Black Granite Tiles</h4>
    <p>Ut wisi enim ad minim veniam quis nostrud exerci..</p>
    <div class="price">Unit Price:<b>US $ 28 / Sq Mtr Min</b></div>
  </article>
</section>

<section class="box" style="left:120px">
  <h3>Delivery</h3>
  <div class="abs" role="img" aria-label="Illustration of a delivery truck" style="left:15px;top:44px;width:66px;height:48px;border-radius:6px;background:linear-gradient(90deg,#3f82c4 0 30%,#c9c9c9 30%)"></div>
  <p class="abs" style="left:96px;top:42px;width:175px">Ut wisi enim ad minim veniam, quis nostrud exerci ...</p>
  <a class="abs" href="#" style="left:96px;top:95px;font-size:11px;font-weight:600;color:#222">LEARN MORE &gt;&gt;</a>
</section>

<section class="box" style="left:415px">
  <h3 style="left:19px">Testimonials</h3>
  <div class="abs" role="img" aria-label="Customer portrait" style="left:19px;top:44px;width:60px;height:56px;background:#e2e2e2;border:1px solid #ccc"></div>
  <p class="abs" style="left:85px;top:42px;width:185px;font-style:italic">“ Ut wisi enim ad minim veniam, quis nostrud exerci nibh euismod tincidunt ut volutpat...”</p>
  <span class="abs" style="right:26px;top:96px;font-size:12px;font-style:italic;font-weight:600;color:var(--green)">By Daniel</span>
</section>

<section class="box" style="left:710px">
  <h3>Newsletter Sign Up</h3>
  <div class="abs" role="img" aria-label="Illustration of a pencil on paper" style="left:14px;top:42px;width:48px;height:50px;background:linear-gradient(135deg,#f0d6c0,#e27a4a)"></div>
  <div class="signup-field">Enter Email Address</div>
  <a class="signup-btn" href="#">SIGN UP</a>
</section>

<footer class="site-footer">
  <div class="abs" style="left:125px;top:18px;display:flex;align-items:center;gap:6px">
    <span style="width:12px;height:12px;background:#fff"></span>
    <span style="font-size:12px;font-weight:700;color:#fff">Copper Ridge Marmora</span>
  </div>
  <small class="abs" style="left:120px;top:66px">Copyright ©2013 .All Right Reserved</small>
  <div class="abs" style="left:471px;top:7px">
    <h5>Contact Us</h5>
    <small style="display:block;margin-top:1px">Company Name Inc<br>417 Quarry Lane, Eastmoor<br>EM2 7QT</small>
  </div>
  <div class="abs" style="left:655px;top:29px;display:flex;align-items:center;gap:10px;font-size:13px;color:#ddd">
    <svg width="15" height="15" viewBox="0 0 15 15"><rect width="15" height="15" rx="2" fill="#888"/><path d="M4 3c-1 1 0 5 4 8 2 1 3 1 4 0l-2-2-1 1c-2-1-3-2-4-4l1-1z" fill="#000"/></svg>
    1800 555 0142
  </div>
  <div class="abs" style="left:655px;top:60px;display:flex;align-items:center;gap:10px;font-size:11px;color:#ccc">
    <svg width="16" height="11" viewBox="0 0 16 11"><rect width="16" height="11" fill="#888"/><path d="M0 0l8 6 8-6" fill="none" stroke="#000" stroke-width="1.2"/></svg>
    info@copperridgemarmora.com
  </div>
  <div class="abs" style="left:839px;top:7px">
    <h5>Connect Us</h5>
    <div class="social"><span></span><span></span><span></span><span></span></div>
  </div>
</footer>

</body>
</html>
```